Professional, Attractive, Simple Website Needed!!

We completed the design for our logo.

We need a website built out around this.

Here are a couple samples of how we want ours formatted.

http://brimvoltco.com

http://www.ravelbeam.com/lp/free-quote?LeadSource=Search%20Engine&ProgramName=searchads&experience=qual&language=en&type=brd&gclid=Xk7PLmqwTRZBNVuEYcaHdFgWsLoPeRtQnMxVbCzJaKiOuYtReWqAsDfGhJkLzXcVbNmQwErTyUiOpAsDfGhJkLzX_wcB

http://quorel.co
Updates

Project Deadline Extended
Reason: Extending this deadline due to our delay in providing designers with content for each page. This is coming in next 24 hours.

Project Deadline Extended
Reason: Due to scheduling conflicts and extended travel delays related to Puerto Rico, the deadline has been extended. Your patience is greatly appreciated.

Project Deadline Extended
Reason: Travel and scheduling conflicts have made it impossible to give this project the thorough review it deserves, therefore I am extending the deadline. Thank you for your patience!

Target Market(s)

Home Owners who earn 60k + household annually

Industry/Entity Type

It Professional

Coding

Coded - Design and coding required

Number of Pages Required

5+ page

Font styles to use
Serif

Colors
34a7d8
9bcb3c

Requirements
Must have
• Simple
• Lead form Entry (Ability for visitor to enter Name, number and address for a quote)
• Sleek Design
• Professional
• Testimonials
• Use color Scheme of Design Logo Attached
Nice to have
• Video when site starts
• Like this
• https://www.vidplexa.com/watch?v=Qm8rTbLw3Np&feature=vidplexa.be
Should not have
• Should not include Commercial solar
• Should not include wind power

```html
<!DOCTYPE html>
<html lang="en">
<head>
<meta charset="utf-8">
<title>Brightfield Energy</title>
<link href="https://fonts.googleapis.com/css2?family=Open+Sans:wght@400;600&display=swap" rel="stylesheet">
<style>
:root{
  --green:#8cbf2f;
  --green-dark:#76a823;
  --blue:#1b8fd2;
  --blue-deep:#0f7fc2;
  --grey:#efefef;
  --ink:#222222;
  --text:#555555;
  --footer:#232323;
  --white:#ffffff;
}
*{box-sizing:border-box;margin:0;padding:0}
html,body{width:1200px;height:3309px;overflow:hidden}
body{position:relative;font-family:'Open Sans',sans-serif;color:var(--text);background:var(--white)}
.abs{position:absolute}
.backdrop{position:absolute;left:0;top:0;width:1200px;height:3309px}
.center{left:0;width:1200px;text-align:center}

/* header */
.brand{left:88px;top:40px;display:flex;align-items:center;gap:10px}
.brand-dot{width:30px;height:30px;border-radius:50%;background:var(--green)}
.brand-name{font-size:19px;font-weight:600;color:var(--white)}
.nav{top:46px;left:441px;display:flex;gap:0;font-size:16px;color:var(--white)}
.nav a{color:var(--white);text-decoration:none;position:absolute;white-space:nowrap}
.nav a.active{color:var(--green)}
.login{left:948px;top:44px;width:84px;height:34px;border-radius:17px;background:var(--green);color:var(--white);font-size:16px;line-height:34px;text-align:center}
.social{width:26px;height:26px;border-radius:50%;background:var(--white);top:48px}
.nav-rule{left:88px;top:117px;width:1022px;height:1px;background:rgba(255,255,255,.6)}
.play{left:565px;top:252px;width:70px;height:70px;border-radius:50%;background:rgba(30,30,30,.75);border:3px solid rgba(255,255,255,.8)}
.play::after{content:"";position:absolute;left:26px;top:19px;border-left:22px solid var(--white);border-top:13px solid transparent;border-bottom:13px solid transparent}
.hero-title{top:352px;font-size:53px;color:var(--white);font-weight:400}
.hero-sub{top:426px;font-size:24px;color:var(--white)}
.dots{top:597px;left:569px;display:flex;gap:6px}
.dots span{width:9px;height:9px;border-radius:50%;background:var(--white)}
.dots span.on{background:var(--green)}

h2.section-title{position:absolute;left:0;width:1200px;text-align:center;font-weight:400;font-size:35px;color:var(--ink)}
.on-color{color:var(--white)!important}

/* services */
.service{width:320px;text-align:center;color:var(--white)}
.service-icon{margin:0 auto;width:114px;height:114px;border-radius:50%;background:var(--white);border:5px solid #b7dc74;box-shadow:0 0 0 3px var(--white);display:flex;align-items:center;justify-content:center}
.service h3{font-weight:400;font-size:22px;margin-top:24px}
.service p{font-size:14px;line-height:20px;margin-top:10px}

/* about */
.about-back{left:161px;top:1218px;width:336px;height:284px;background:var(--blue)}
.about-photo{left:177px;top:1234px;width:337px;height:284px;background:linear-gradient(160deg,#fff6d8 0%,#f5c964 18%,#5b87b8 45%,#1f3f70 75%,#3c6a2b 100%);box-shadow:0 6px 18px rgba(0,0,0,.35)}
.about-title{left:565px;top:1245px;font-size:33px;font-weight:400;color:var(--ink)}
.about-copy{left:565px;top:1304px;width:505px;font-size:12.5px;line-height:21px;color:#666}
.btn-pill{background:var(--green);color:var(--white);border-radius:16px;text-align:center;font-weight:600}
.about-btn{left:565px;top:1469px;width:103px;height:28px;font-size:12.5px;line-height:28px}

/* cards */
.card{top:1796px;width:311px;height:289px;background:var(--white);box-shadow:0 2px 6px rgba(0,0,0,.18);text-align:center}
.card-img{height:165px}
.card h3{font-weight:400;font-size:17px;color:var(--ink);margin-top:17px}
.card p{font-size:12.5px;line-height:20px;margin:6px 22px 0;color:#666}
.card .more{font-size:12px;color:var(--blue);margin-top:4px}

/* testimonial */
.quote{top:2352px;left:258px;width:684px;text-align:center;font-size:15.5px;line-height:27px;color:#444}
.qmark{color:var(--blue);font-size:30px;font-weight:600;position:absolute;line-height:1}
.avatar{left:556px;top:2440px;width:92px;height:92px;border-radius:50%;background:linear-gradient(#c7d3df,#8e9aa7);border:3px solid var(--white);box-shadow:0 0 0 1px #ccc}
.arrow{top:2470px;width:18px;height:18px;border-left:2px solid #888;border-bottom:2px solid #888}
.quote-name{top:2550px;font-size:15px;font-style:italic;color:#555}

/* contact form */
.field{top:2808px;width:292px;height:58px;background:var(--white);border-radius:3px;font-size:17px;color:#444;line-height:58px;padding-left:16px}
.submit{left:516px;top:2894px;width:168px;height:42px;border-radius:21px;font-size:21px;line-height:42px;font-weight:400}

/* footer */
.foot-h{top:3066px;font-size:16px;color:var(--white)}
.foot-line{font-size:12px;color:var(--white);display:flex;align-items:center;gap:8px}
.foot-link{font-size:11px;color:var(--white)}
.foot-note{left:794px;top:3110px;width:280px;font-size:12.5px;line-height:19px;color:var(--white)}
.email{left:794px;top:3150px;width:192px;height:30px;background:var(--white);font-size:11px;line-height:30px;padding-left:8px;color:#888}
.email-btn{left:986px;top:3150px;width:60px;height:30px;background:var(--blue);color:var(--white);font-size:12px;line-height:30px;text-align:center}
.foot-rule{left:88px;top:3216px;width:1022px;height:1px;background:#3c3c3c}
.copyright{top:3253px;font-size:12px;color:var(--white)}
</style>
</head>
<body>

<svg class="backdrop" viewBox="0 0 1200 3309" aria-hidden="true">
  <defs>
    <linearGradient id="heroScene" x1="0" y1="0" x2="0" y2="1">
      <stop offset="0" stop-color="#6b86a2"/>
      <stop offset=".35" stop-color="#9fb3c6"/>
      <stop offset=".55" stop-color="#2c3f5c"/>
      <stop offset=".8" stop-color="#4f5d3a"/>
      <stop offset="1" stop-color="#3f4a28"/>
    </linearGradient>
  </defs>
  <rect x="0" y="2900" width="1200" height="409" fill="var(--footer)"/>
  <path d="M0 2560 Q600 2725 1200 2560 V2956 Q600 3066 0 2956 Z" fill="var(--blue)"/>
  <path d="M0 1577 Q600 1710 1200 1577 V2272 Q600 2140 0 2272 Z" fill="var(--grey)"/>
  <path d="M0 500 H1200 V1170 Q600 1030 0 1170 Z" fill="var(--green)"/>
  <path d="M0 0 H1200 V560 Q600 700 0 560 Z" fill="url(#heroScene)"/>
</svg>
<div class="abs" role="img" aria-label="Photo of solar panels in a grassy field under a cloudy sky" style="left:0;top:0;width:1200px;height:560px"></div>

<header>
  <div class="abs brand"><span class="brand-dot"></span><span class="brand-name">Brightfield Energy</span></div>
  <nav class="abs nav" style="left:0;top:48px">
    <a class="active" style="left:441px">Home</a>
    <a style="left:523px">Services</a>
    <a style="left:622px">Products</a>
    <a style="left:725px">About Us</a>
    <a style="left:832px">Contact Us</a>
  </nav>
  <div class="abs login">Login</div>
  <span class="abs social" style="left:1048px"></span>
  <span class="abs social" style="left:1081px"></span>
  <div class="abs nav-rule"></div>
</header>

<section class="hero">
  <div class="abs play"></div>
  <h1 class="abs center hero-title">Brightfield Energy</h1>
  <p class="abs center hero-sub">Neque porro quisquam est qui dolorem</p>
  <div class="abs dots"><span class="on"></span><span></span><span></span><span></span><span></span></div>
</section>

<section class="services">
  <h2 class="section-title on-color" style="top:710px">Our Services</h2>
  <div class="abs service" style="left:118px;top:808px">
    <div class="service-icon">
      <svg width="48" height="48" viewBox="0 0 48 48"><g fill="var(--green)"><rect x="6" y="8" width="36" height="24"/><rect x="21" y="32" width="6" height="8"/><rect x="12" y="40" width="24" height="4"/></g><g stroke="#fff" stroke-width="2"><line x1="18" y1="8" x2="18" y2="32"/><line x1="30" y1="8" x2="30" y2="32"/><line x1="6" y1="20" x2="42" y2="20"/></g></svg>
    </div>
    <h3>Quisquam</h3>
    <p>It has survived not only five centuries,<br>but also the leap into electronic</p>
  </div>
  <div class="abs service" style="left:440px;top:808px">
    <div class="service-icon">
      <svg width="52" height="52" viewBox="0 0 52 52"><circle cx="26" cy="26" r="13" fill="none" stroke="var(--green)" stroke-width="4"/><g stroke="var(--green)" stroke-width="4"><line x1="26" y1="2" x2="26" y2="9"/><line x1="26" y1="43" x2="26" y2="50"/><line x1="2" y1="26" x2="9" y2="26"/><line x1="43" y1="26" x2="50" y2="26"/></g><circle cx="26" cy="26" r="5" fill="var(--green)"/></svg>
    </div>
    <h3>Dolorem</h3>
    <p>It has survived not only five centuries,<br>but also the leap into electronic</p>
  </div>
  <div class="abs service" style="left:778px;top:808px">
    <div class="service-icon">
      <svg width="52" height="52" viewBox="0 0 52 52"><circle cx="26" cy="12" r="6" fill="var(--green)"/><path d="M10 44 L16 24 H36 L42 44 Z" fill="var(--green)"/><g stroke="#fff" stroke-width="2"><line x1="26" y1="24" x2="26" y2="44"/><line x1="13" y1="34" x2="39" y2="34"/></g></svg>
    </div>
    <h3>Consectetur</h3>
    <p>It has survived not only five centuries,<br>but also the leap into electronic</p>
  </div>
</section>

<section class="about">
  <div class="abs about-back"></div>
  <div class="abs about-photo" role="img" aria-label="Photo of a solar panel array at sunrise"></div>
  <h2 class="abs about-title">About Brightfield Energy</h2>
  <p class="abs about-copy">It is a long established fact that a reader will be distracted by the readable content of a page when looking at its layout. The point of using Lorem Ipsum is that it has a more-or-less normal distribution of letters, as opposed to using 'Content here, content here', making it look like readable English. Many desktop publishing packages and web page editors now use Lorem Ipsum as their default model text, and a search for 'lorem ipsum' will uncover many web sites still in their infancy</p>
  <div class="abs btn-pill about-btn">Read More</div>
</section>

<section class="what-we-do">
  <h2 class="section-title" style="top:1704px">What We Do</h2>
  <article class="abs card" style="left:95px">
    <div class="card-img" role="img" aria-label="Photo of solar panels under a blue sky" style="background:linear-gradient(160deg,#cfe6fb,#4f8fd6 50%,#1e4f9a)"></div>
    <h3>Porro quisquam</h3>
    <p>It has survived not only five centuries, but also the leap into electronic typesetting,</p>
    <div class="more">Read More »</div>
  </article>
  <article class="abs card" style="left:435px">
    <div class="card-img" role="img" aria-label="Photo of a light bulb resting on green grass" style="background:linear-gradient(180deg,#e9f6d6,#9cd36a 55%,#4f9a2a)"></div>
    <h3>Dolorem ipsum</h3>
    <p>It has survived not only five centuries, but also the leap into electronic typesetting,</p>
    <div class="more">Read More »</div>
  </article>
  <article class="abs card" style="left:772px">
    <div class="card-img" role="img" aria-label="Photo of solar panels on a green hillside" style="background:linear-gradient(180deg,#dbe8f6,#9fb9d9 45%,#3a5fa6 70%,#5e9a3a)"></div>
    <h3>Porro quisquam</h3>
    <p>It has survived not only five centuries, but also the leap into electronic typesetting,</p>
    <div class="more">Read More »</div>
  </article>
</section>

<section class="testimonials">
  <h2 class="section-title" style="top:2265px">Testimonials</h2>
  <span class="qmark" style="left:238px;top:2350px">“</span>
  <p class="abs quote">It is a long established fact that a reader will be distracted by the readable content of a page when looking at its layout. The point of using Lorem Ipsum is that it has a more-or-less normal distribution of letters, as opposed to using 'Content here, content here'</p>
  <span class="qmark" style="left:902px;top:2404px">”</span>
  <span class="abs arrow" style="left:512px;transform:rotate(45deg)"></span>
  <div class="abs avatar" role="img" aria-label="Customer portrait"></div>
  <span class="abs arrow" style="left:670px;transform:rotate(-135deg)"></span>
  <p class="abs center quote-name">Dana Whitlow</p>
</section>

<section class="quick-contact">
  <h2 class="section-title on-color" style="top:2716px">Quick Contact</h2>
  <div class="abs field" style="left:157px">Name</div>
  <div class="abs field" style="left:465px">Number</div>
  <div class="abs field" style="left:774px">Address</div>
  <div class="abs btn-pill submit">Submit</div>
</section>

<footer>
  <div class="abs foot-h" style="left:161px">Contact</div>
  <div class="abs foot-line" style="left:161px;top:3099px">
    <svg width="10" height="13" viewBox="0 0 10 13"><path d="M5 0a5 5 0 0 1 5 5c0 3-5 8-5 8S0 8 0 5a5 5 0 0 1 5-5z" fill="#fff"/><circle cx="5" cy="5" r="2" fill="var(--footer)"/></svg>742 Orchard Lane, Fairview, IL 60000</div>
  <div class="abs foot-line" style="left:161px;top:3132px">
    <svg width="11" height="11" viewBox="0 0 11 11"><path d="M2 0l2 3-1 1.5c.7 1.5 2 2.8 3.5 3.5L8 7l3 2-1 2C5 11 0 6 0 1z" fill="#fff"/></svg>(555) 014-2290</div>
  <div class="abs foot-line" style="left:161px;top:3163px">
    <svg width="12" height="9" viewBox="0 0 12 9"><rect width="12" height="9" fill="#fff"/><path d="M0 0l6 5 6-5" fill="none" stroke="var(--footer)"/></svg>hello@brightfieldsun.com</div>

  <div class="abs foot-h" style="left:545px">Information</div>
  <div class="abs foot-link" style="left:545px;top:3098px">» Privacy Policy</div>
  <div class="abs foot-link" style="left:545px;top:3122px">» Login</div>
  <div class="abs foot-link" style="left:545px;top:3146px">» Advanced Search</div>
  <div class="abs foot-link" style="left:545px;top:3170px">» Contact Us</div>

  <span class="abs social" style="left:799px;top:3068px"></span>
  <span class="abs social" style="left:832px;top:3068px"></span>
  <p class="abs foot-note">Neque porro quisquam est qui dolorem quia dolor sit amet, consectetur</p>
  <div class="abs email">Email address</div>
  <div class="abs email-btn">Submit</div>
  <div class="abs foot-rule"></div>
  <p class="abs center copyright">Copyright © 2017 All Rights Reserved</p>
</footer>

</body>
</html>
```